Website for a Steadwell, an HVAC company.

We are a company that provides residential and commercial service. We don’t need any widgets other than a call to action where customers can message us. Though we have very few google reviews, they are all great and would like to see those populated. Simple and modern is the style. I included our logo and a pic of our vans.

Target Market(s)

Residential customers

Coding

Coded - Design and coding required

Number of Pages Required

1 page

Font styles to use
Sans Serif

Colors
0054AA
0677BA
7BADD7
CADEEF
E8F1F8
EE7325
F08F49
F5BC92
FAE3D3
FDF4ED

```html
<!DOCTYPE html>
<html lang="en">
<head>
<meta charset="utf-8">
<title>Steadwell Heating and Air</title>
<link href="https://fonts.googleapis.com/css2?family=Oswald:wght@500;600&family=Poppins:wght@400;500;600;700&display=swap" rel="stylesheet">
<style>
:root{
  --blue:#0054AA;--blue-2:#0677BA;--blue-3:#7BADD7;--blue-4:#CADEEF;--blue-5:#E8F1F8;
  --orange:#EE7325;--orange-2:#F08F49;--orange-3:#F5BC92;--orange-4:#FAE3D3;--orange-5:#FDF4ED;
  --gold:#F2B233;--ink:#1b1b1b;--text:#666;--grey:#f1f1f1;--field:#ececec;
}
*{margin:0;padding:0;box-sizing:border-box}
html,body{width:1200px;height:4827px;overflow:hidden}
body{position:relative;background:#fff;font-family:'Poppins',sans-serif;color:var(--text)}
.abs{position:absolute}
h1,h2,h3,.cond{font-family:'Oswald',sans-serif;font-weight:600;color:var(--ink);text-transform:uppercase;letter-spacing:.2px}
p{font-size:13.5px;line-height:22.5px}
.btn{position:absolute;display:flex;align-items:center;justify-content:center;font-weight:600;font-size:13px;text-transform:uppercase;color:#fff;text-decoration:none}
.btn-blue{background:var(--blue)}
.btn-orange{background:linear-gradient(90deg,var(--gold),var(--orange))}
.photo{position:absolute}
.bg-shapes{position:absolute;left:0;top:0}

/* header */
.brand{left:88px;top:30px;width:118px;text-align:center;color:#fff}
.brand .dot{width:30px;height:30px;border-radius:50%;background:var(--orange);margin:0 auto 10px}
.brand .name{font-weight:700;font-size:12px;letter-spacing:2px}
.brand .tag{font-size:6.5px;letter-spacing:2px;font-weight:600}
.nav{left:459px;top:56px}
.nav a{font-family:'Oswald',sans-serif;font-weight:500;font-size:13.5px;color:#fff;text-decoration:none;text-transform:uppercase;position:absolute;white-space:nowrap}
.nav a.active{color:var(--orange-2)}
.contact-btn{left:971px;top:49px;width:141px;height:37px;font-size:13.5px}

/* hero */
.hero-title{left:88px;top:205px;font-size:72px;line-height:82px;color:#fff;white-space:nowrap}
.hero-title span{display:block;color:transparent;background:linear-gradient(90deg,var(--gold),var(--orange));-webkit-background-clip:text;background-clip:text}
.hero-sub{left:92px;top:385px;font-size:33px;line-height:40px;color:#fff;font-weight:500}
.explore{left:94px;top:444px;width:159px;height:47px}
.request{left:264px;top:444px;width:220px;height:47px;border:2px solid #fff}

/* intro */
.intro-title{left:0;top:676px;width:1200px;text-align:center;font-size:37px;line-height:40px}
.feature{position:absolute;top:795px;width:200px;text-align:center}
.feature .icon{width:85px;height:85px;margin:0 auto;background:#eeeeee;display:flex;align-items:center;justify-content:center}
.feature h3{font-size:17px;margin-top:30px}

/* welcome */
.dots{left:290px;top:1468px;width:100px;height:70px;background-image:radial-gradient(var(--orange) 1.6px,transparent 1.8px);background-size:10px 10px}
.welcome h2{font-size:38px;position:absolute;left:598px;top:1048px}
.welcome p{position:absolute;left:598px;width:476px}
.read-more{left:598px;top:1406px;width:141px;height:47px}

/* tailored */
.tailored-title{left:0;top:1780px;width:1200px;text-align:center;font-size:37px}
.space{position:absolute;top:1867px;width:460px}
.space .sq{width:99px;height:99px;background:linear-gradient(135deg,var(--gold),var(--orange));display:flex;align-items:center;justify-content:center}
.space h3{font-size:28px;margin-top:30px;font-weight:500}
.space p{margin-top:10px}

/* timely */
.timely-mark{left:106px;top:2310px;width:56px;height:56px;border-radius:50%;background:linear-gradient(135deg,var(--orange-2),var(--blue-2))}
.timely h2{position:absolute;left:103px;top:2388px;font-size:38px}
.timely p{position:absolute;left:103px;top:2454px;width:510px}
.schedule{left:105px;top:2588px;width:253px;height:45px}

/* services cards */
.services-title{left:0;top:2798px;width:1200px;text-align:center;font-size:37px;color:#fff}
.card{position:absolute;top:2872px;width:471px;height:372px;background:#fff}
.card .pic{height:269px}
.card h3{font-size:19px;line-height:24px;font-weight:500;margin:17px 0 0 27px}
.card p{margin:5px 0 0 27px;width:390px;font-size:12.5px;line-height:21px}
.card .arrow{position:absolute;right:30px;bottom:-15px;width:35px;height:33px;background:var(--blue);display:flex;align-items:center;justify-content:center}

/* testimonial */
.test-title{left:0;top:3494px;width:1200px;text-align:center;font-size:35px}
.quote{left:561px;top:3566px;width:79px;height:79px;background:var(--blue);display:flex;align-items:center;justify-content:center}
.test-text{left:206px;top:3672px;width:788px;text-align:center}
.test-name{left:0;top:3750px;width:1200px;text-align:center;font-size:13px}
.pager{left:578px;top:3782px;display:flex;gap:8px}
.pager i{width:8px;height:8px;background:#ddd;display:block}
.pager i.on{background:#111}
.divider{left:105px;top:3844px;width:990px;height:1px;background:#e6e6e6}

/* contact */
.contact-title{left:0;top:3905px;width:1200px;text-align:center;font-size:37px}
.field{position:absolute;background:var(--field);font-size:13px;color:#555;padding:14px 0 0 21px;font-weight:500}
.submit{left:527px;top:4243px;width:144px;height:45px;font-size:15px}

/* footer */
.foot-brand{left:178px;top:4540px;width:210px;text-align:center;color:#fff}
.foot-brand .dot{width:74px;height:74px;border-radius:50%;background:var(--orange);margin:0 auto 26px}
.foot-brand .name{font-weight:700;font-size:22px;letter-spacing:5px}
.foot-brand .tag{font-weight:600;font-size:11px;letter-spacing:3.4px}
.foot-col{position:absolute;top:4508px;color:#fff}
.foot-col h4{font-size:17px;font-weight:600;margin-bottom:16px}
.foot-col li{list-style:none;font-size:12px;line-height:31px;color:#ddd}
.foot-col li::before{content:"›";color:#999;margin-right:9px}
.info{font-size:12px;color:#ddd;line-height:17px;display:flex;gap:10px;margin-bottom:14px}
.news-input{position:absolute;left:849px;top:4607px;width:263px;height:50px;background:#2d2d2d;display:flex;align-items:center;padding:0 18px;font-size:12px;color:#ddd;justify-content:space-between}
.foot-line{left:88px;top:4770px;width:1024px;height:1px;background:#333}
.copyright{left:0;top:4792px;width:1200px;text-align:center;font-size:12px;font-weight:600;color:#fff}
.to-top{left:1132px;top:4749px;width:38px;height:38px;border-radius:50%;background:var(--blue);display:flex;align-items:center;justify-content:center}
</style>
</head>
<body>

<svg class="bg-shapes" width="1200" height="4827" viewBox="0 0 1200 4827" aria-hidden="true">
  <defs>
    <linearGradient id="heroBlue" x1="0" y1="0" x2="1" y2="1">
      <stop offset="0" stop-color="#0a58b8"/><stop offset="1" stop-color="#0047a0"/>
    </linearGradient>
    <linearGradient id="warm" x1="0" y1="0" x2="1" y2="0">
      <stop offset="0" stop-color="#F2B233"/><stop offset="1" stop-color="#E0571C"/>
    </linearGradient>
  </defs>
  <polygon points="0,665 1200,475 1200,600 0,700" fill="url(#warm)"/>
  <polygon points="0,0 1200,0 1200,470 0,685" fill="url(#heroBlue)"/>
  <polygon points="0,1556 700,1640 1200,1560 1200,2200 0,2200" fill="#f2f2f2"/>
  <polygon points="0,2812 1200,2588 1200,3240 0,3520" fill="url(#warm)"/>
  <polygon points="1200,3240 1200,3440 620,3440" fill="#0054AA"/>
  <polygon points="960,3960 1200,3810 1200,4120" fill="#FDF4ED"/>
  <polygon points="0,4330 760,4420 0,4495" fill="url(#warm)"/>
  <polygon points="0,4495 1200,4385 1200,4827 0,4827" fill="#1b1b1b"/>
</svg>

<!-- hero van sits behind the headline -->
<div class="photo" role="img" aria-label="Black company service van with branding" style="left:575px;top:135px;width:625px;height:475px;background:linear-gradient(160deg,#2a2a2a,#0e0e0e 70%);border-radius:60px 0 0 40px"></div>

<!-- header -->
<div class="abs brand"><div class="dot"></div><div class="name">STEADWELL</div><div class="tag">HEATING AND AIR</div></div>
<nav class="abs nav">
  <a class="active" style="left:0">Home</a>
  <a style="left:60px">About Us</a>
  <a style="left:147px">Services</a>
  <a style="left:229px">Special Offer</a>
  <a style="left:343px">Our Work</a>
  <a style="left:434px">Reviews</a>
</nav>
<a class="btn btn-orange contact-btn">Contact Us</a>

<!-- hero -->
<h1 class="abs hero-title">Reliable<span>HVAC Solutions</span></h1>
<div class="abs cond hero-sub">For Your Home &amp; Business</div>
<a class="btn btn-orange explore">Explore More</a>
<a class="btn request">Request Our Services</a>

<!-- intro -->
<h2 class="abs intro-title">Air Conditioning Repair,<br>Heating Service &amp; Installation</h2>
<div class="feature" style="left:178px"><div class="icon"><svg width="46" height="46" viewBox="0 0 46 46" fill="none" stroke="#333" stroke-width="2"><rect x="5" y="8" width="36" height="16" rx="2"/><path d="M9 18h28M14 30v8M23 30v10M32 30v8"/></svg></div><h3>AC Installation</h3></div>
<div class="feature" style="left:382px"><div class="icon"><svg width="46" height="46" viewBox="0 0 46 46" fill="none" stroke="#333" stroke-width="2"><circle cx="23" cy="20" r="13"/><path d="M14 29l-6 8M32 29l6 8M18 15l10 10M28 15L18 25"/><path d="M8 38h30" stroke="#EE7325"/></svg></div><h3>AC Maintenance</h3></div>
<div class="feature" style="left:588px"><div class="icon"><svg width="46" height="46" viewBox="0 0 46 46" fill="none" stroke="#333" stroke-width="2"><rect x="8" y="16" width="22" height="20" rx="3"/><path d="M30 22h6v8h-6M14 16v-5h10v5"/><path d="M36 6v12" stroke="#EE7325"/></svg></div><h3>Heating Service</h3></div>
<div class="feature" style="left:808px"><div class="icon"><svg width="46" height="46" viewBox="0 0 46 46" fill="none" stroke="#333" stroke-width="2"><path d="M6 22L23 8l17 14M11 19v19h24V19"/><path d="M16 27h14M16 32h10" stroke="#EE7325"/></svg></div><h3>Indoor Air Quality</h3></div>

<!-- welcome -->
<section class="welcome">
  <div class="photo" role="img" aria-label="Technicians installing a ceiling air conditioning unit" style="left:124px;top:1003px;width:375px;height:460px;background:linear-gradient(150deg,#c9d3dc,#5d6a78)"></div>
  <div class="photo" role="img" aria-label="Technician servicing an outdoor condenser unit" style="left:351px;top:1249px;width:205px;height:260px;background:linear-gradient(150deg,#8a9aa3,#3f5468);box-shadow:0 10px 30px rgba(0,0,0,.2)"></div>
  <div class="abs dots"></div>
  <h2>Welcome to Steadwell</h2>
  <p style="top:1108px">It is a long established fact that a reader will be distracted by the readable content of a page when looking at its layout. The point of using Lorem Ipsum is that it has a more-or-less normal distribution of letters, as opposed to using 'Content here, content here', making it look like readable English. Many desktop publishing packages and web page editors now use Lorem Ipsum as their default model text, and a search for 'lorem ipsum' will uncover many web sites still in their infancy.</p>
  <p style="top:1292px">There are many variations of passages of Lorem Ipsum available, but the majority have suffered alteration in some form, by injected humour, or randomised words which don't look even slightly believable. If you are going to use a passage of Lorem Ipsum,</p>
  <a class="btn btn-blue read-more">Read More</a>
</section>

<!-- tailored -->
<div class="photo" role="img" aria-label="Two branded service vans parked side by side" style="left:785px;top:1560px;width:385px;height:200px;background:linear-gradient(160deg,#2b2b2b,#111);border-radius:40px 40px 20px 20px"></div>
<h2 class="abs tailored-title">Tailored Services for Every Space</h2>
<div class="space" style="left:139px">
  <div class="sq"><svg width="50" height="50" viewBox="0 0 50 50" fill="none" stroke="#333" stroke-width="2"><rect x="10" y="8" width="30" height="36"/><path d="M16 14h5M29 14h5M16 22h5M29 22h5M16 30h5M29 30h5M21 44v-8h8v8"/></svg></div>
  <h3>Commercial Service</h3>
  <p>It is a long established fact that a reader will be distracted by the readable content of a page when looking at its layout. The point of using Lorem Ipsum is that it has a more-or-less normal distribution of letters, as opposed to using 'Content here, content here',</p>
</div>
<div class="space" style="left:646px">
  <div class="sq"><svg width="50" height="50" viewBox="0 0 50 50" fill="none" stroke="#333" stroke-width="2"><path d="M6 24L25 8l19 16M11 20v24h28V20"/><rect x="20" y="30" width="10" height="14"/></svg></div>
  <h3>Residential Service</h3>
  <p>It is a long established fact that a reader will be distracted by the readable content of a page when looking at its layout. The point of using Lorem Ipsum is that it has a more-or-less normal distribution of letters, as opposed to using 'Content here, content here',</p>
</div>

<!-- timely -->
<div class="photo" role="img" aria-label="Smiling technician in a hard hat holding a laptop, with flame graphics behind" style="left:640px;top:2194px;width:540px;height:478px;background:linear-gradient(120deg,#f2b233 0%,#ee7325 30%,#2a4f86 55%,#1c3660);clip-path:polygon(8% 20%,60% 0,80% 10%,100% 40%,100% 100%,0 100%)"></div>
<section class="timely">
  <div class="abs timely-mark"></div>
  <h2>Timely. Honest. Professional.</h2>
  <p>It is a long established fact that a reader will be distracted by the readable content of a page when looking at its layout. The point of using Lorem Ipsum is that it has a more-or-less normal distribution of letters, as opposed to using 'Content here, content here', making it look like readable English. Many desktop publishing</p>
  <a class="btn btn-blue schedule">Schedule an Appointment</a>
</section>

<!-- services -->
<h2 class="abs services-title">Our Services</h2>
<article class="card" style="left:120px">
  <div class="pic" role="img" aria-label="Technician repairing a ceiling air conditioner" style="background:linear-gradient(160deg,#dfe3e6,#7d8a96)"></div>
  <h3>AC Repair</h3>
  <p>It is a long established fact that a reader will be distracted by the readable content of a page</p>
  <span class="arrow"><svg width="12" height="12" viewBox="0 0 12 12" fill="none" stroke="#fff" stroke-width="2"><path d="M4 2l4 4-4 4"/></svg></span>
</article>
<article class="card" style="left:609px">
  <div class="pic" role="img" aria-label="Technician with red gloves servicing a wall-mounted boiler" style="background:linear-gradient(160deg,#c9c9c9,#6b5a55)"></div>
  <h3>About Heating</h3>
  <p>It is a long established fact that a reader will be distracted by the readable content of a page</p>
  <span class="arrow"><svg width="12" height="12" viewBox="0 0 12 12" fill="none" stroke="#fff" stroke-width="2"><path d="M4 2l4 4-4 4"/></svg></span>
</article>

<!-- testimonial -->
<h2 class="abs test-title">What Our Clients Says</h2>
<div class="abs quote"><svg width="40" height="32" viewBox="0 0 40 32" fill="#fff"><path d="M2 18C2 8 8 2 16 1v6c-4 1-6 4-6 8h6v15H2zM24 18c0-10 6-16 14-17v6c-4 1-6 4-6 8h6v15H24z"/></svg></div>
<p class="abs test-text">It is a long established fact that a reader will be distracted by the readable content of a page when looking at its layout. The point of using Lorem Ipsum is that it has a more-or-less normal distribution of letters, as opposed to using 'Content here, content here', making it look like readable English.</p>
<div class="abs cond test-name">Mara Ellis</div>
<div class="abs pager"><i></i><i class="on"></i><i></i></div>
<div class="abs divider"></div>

<!-- contact -->
<h2 class="abs contact-title">Contact Us</h2>
<div class="field" style="left:300px;top:3975px;width:293px;height:46px">Frist Name</div>
<div class="field" style="left:606px;top:3975px;width:294px;height:46px">Last Name</div>
<div class="field" style="left:300px;top:4035px;width:293px;height:46px">Email Address</div>
<div class="field" style="left:606px;top:4035px;width:294px;height:46px">Phone Number</div>
<div class="field" style="left:300px;top:4095px;width:600px;height:135px">Message...</div>
<a class="btn btn-blue submit">Submit</a>

<!-- footer -->
<div class="abs foot-brand"><div class="dot"></div><div class="name">STEADWELL</div><div class="tag">HEATING AND AIR</div></div>
<div class="foot-col" style="left:426px">
  <h4>Quick links</h4>
  <ul><li>Home</li><li>About Us</li><li>Services</li><li>Our Work</li><li>Contact Us</li></ul>
</div>
<div class="foot-col" style="left:607px">
  <h4>Contact info</h4>
  <div class="info"><svg width="12" height="12" viewBox="0 0 12 12" fill="#fff"><path d="M0 2h12v8H0zM0 2l6 4 6-4" stroke="#1b1b1b"/></svg><div>Email:<br>info@steadwell.com</div></div>
  <div class="info"><svg width="12" height="12" viewBox="0 0 12 12" fill="#fff"><path d="M2 0l3 3-1.5 2a7 7 0 003.5 3.5L9 7l3 3-2 2C5 12 0 7 0 2z"/></svg><div>Phone:<br>(555) 014.2290</div></div>
  <div class="info"><svg width="12" height="14" viewBox="0 0 12 14" fill="#fff"><path d="M6 0a5 5 0 015 5c0 4-5 9-5 9S1 9 1 5a5 5 0 015-5z"/><circle cx="6" cy="5" r="2" fill="#1b1b1b"/></svg><div>Location:<br>48 Harbor Lane, Suite 210<br>Fairview, IL 62911</div></div>
</div>
<div class="foot-col" style="left:849px">
  <h4>Newsletter</h4>
  <p style="font-size:12px;line-height:18px;color:#ddd;width:230px">Subscribe to our email address to get the latest news.</p>
</div>
<div class="news-input"><span>✉&nbsp; Enter Your Email...</span><svg width="14" height="14" viewBox="0 0 14 14" fill="#fff"><path d="M0 6L14 0 9 14 7 8z"/></svg></div>
<div class="abs foot-line"></div>
<div class="abs copyright">© Copyright 2025, All Rights Reserved</div>
<div class="abs to-top"><svg width="12" height="12" viewBox="0 0 12 12" fill="none" stroke="#fff" stroke-width="2"><path d="M2 8l4-4 4 4"/></svg></div>

</body>
</html>
```